Brivolt Technologies business card design

We need a business card designed with our new logo. it would be great if the card could communicate it is a technology based company.

Target Market(s)

system integrators

Industry/Entity Type

technology, IOT

Contact Information for Business Card

Name, designation, Address, telephone number, email address

Requirements
Must have
• logo and company name
Nice to have
• something to do with technology

```html
<!DOCTYPE html>
<html lang="en">
<head>
<meta charset="utf-8">
<title>Brivolt Technologies business card</title>
<link href="https://fonts.googleapis.com/css2?family=Roboto:wght@400;700&display=swap" rel="stylesheet">
<style>
  :root {
    --stage: #e9e6e2;
    --orange-deep: #d24a17;
    --orange-mid: #e35a12;
    --orange-light: #ef7a12;
    --orange-accent: #f39a1f;
    --paper: #ffffff;
    --ink: #3a3a3a;
    --white: #ffffff;
  }
  * { box-sizing: border-box; margin: 0; padding: 0; }
  html, body {
    width: 1200px; height: 900px; overflow: hidden;
    background: var(--stage);
    font-family: "Roboto", Arial, sans-serif;
  }
  .canvas {
    position: relative; width: 1200px; height: 900px;
  }
  .card {
    position: absolute; left: 280px; width: 640px; height: 366px;
    box-shadow: 0 10px 28px rgba(0,0,0,0.18);
    overflow: hidden;
  }
  /* Contact side */
  .card--contact { top: 50px; display: flex; background: var(--paper); }
  .contact__brand-panel {
    width: 250px; height: 100%;
    background: linear-gradient(180deg, var(--orange-deep) 0%, var(--orange-light) 100%);
    display: flex; align-items: center; justify-content: center;
  }
  .brand {
    display: flex; align-items: center; gap: 10px;
    font-weight: 700; letter-spacing: 1px; text-transform: uppercase;
  }
  .brand__mark { width: 16px; height: 16px; }
  .brand--on-orange { color: var(--white); font-size: 17px; }
  .brand--on-orange .brand__mark { background: var(--white); }
  .contact__details {
    flex: 1; padding: 30px 40px 0 44px;
  }
  .brand--on-paper { color: var(--ink); font-size: 22px; justify-content: center; margin-bottom: 30px; }
  .brand--on-paper .brand__mark { background: var(--orange-accent); }
  .contact-list { list-style: none; }
  .contact-list__item {
    display: flex; align-items: center; gap: 22px;
    font-size: 17px; color: var(--ink); height: 44px;
  }
  .contact-list__icon {
    width: 28px; height: 28px; border-radius: 50%;
    background: var(--orange-accent);
    display: flex; align-items: center; justify-content: center; flex-shrink: 0;
  }
  .contact-list__icon svg { width: 16px; height: 16px; }
  .contact-address {
    margin: 6px 0 0 50px; font-size: 17px; line-height: 1.35; color: var(--ink);
  }
  /* Logo side */
  .card--logo {
    top: 484px; background: var(--orange-deep);
    display: flex; align-items: center; justify-content: center;
  }
  .circuit-band {
    position: absolute; left: 0; right: 0; height: 120px;
    background: linear-gradient(90deg, rgba(243,154,31,0.10), rgba(243,154,31,0.22), rgba(243,154,31,0.10));
  }
  .circuit-band--top { top: 0; }
  .circuit-band--bottom { bottom: 0; }
  .brand--hero { position: relative; color: var(--white); font-size: 40px; gap: 16px; }
  .brand--hero .brand__mark { width: 30px; height: 30px; background: var(--white); }
</style>
</head>
<body>
<main class="canvas">

  <section class="card card--contact" aria-label="Business card, contact side">
    <div class="contact__brand-panel">
      <div class="brand brand--on-orange"><span class="brand__mark"></span>Brivolt Technologies</div>
    </div>
    <div class="contact__details">
      <div class="brand brand--on-paper"><span class="brand__mark"></span>Brivolt Technologies</div>
      <ul class="contact-list">
        <li class="contact-list__item">
          <span class="contact-list__icon">
            <svg viewBox="0 0 24 24"><path fill="#fff" d="M6.6 10.8a15 15 0 0 0 6.6 6.6l2.2-2.2a1 1 0 0 1 1-.25 11.4 11.4 0 0 0 3.6.57 1 1 0 0 1 1 1V20a1 1 0 0 1-1 1A17 17 0 0 1 3 4a1 1 0 0 1 1-1h3.5a1 1 0 0 1 1 1c0 1.25.2 2.45.57 3.57a1 1 0 0 1-.25 1z"/></svg>
          </span>+44 (0)117 496 0000
        </li>
        <li class="contact-list__item">
          <span class="contact-list__icon">
            <svg viewBox="0 0 24 24"><rect x="3" y="6" width="18" height="12" rx="1" fill="none" stroke="#fff" stroke-width="2"/><path d="M3 7l9 6 9-6" fill="none" stroke="#fff" stroke-width="2"/></svg>
          </span>sales@brivolttech.com
        </li>
        <li class="contact-list__item">
          <span class="contact-list__icon">
            <svg viewBox="0 0 24 24" fill="none" stroke="#fff" stroke-width="1.8"><circle cx="12" cy="12" r="9"/><path d="M3 12h18M12 3c3 3 3 15 0 18M12 3c-3 3-3 15 0 18"/></svg>
          </span>www.brivolttech.com
        </li>
      </ul>
      <p class="contact-address">Unit 3 Northgate Park<br>Elmwood Green<br>BS7 9QX</p>
    </div>
  </section>

  <section class="card card--logo" aria-label="Business card, logo side">
    <div class="circuit-band circuit-band--top" role="img" aria-label="Faint circuit trace pattern"></div>
    <div class="circuit-band circuit-band--bottom" role="img" aria-label="Faint circuit trace pattern"></div>
    <div class="brand brand--hero"><span class="brand__mark"></span>Brivolt Technologies</div>
  </section>

</main>
</body>
</html>
```